Software Development Consulting Company Needs Business Card Design

We need a new business card design for our consultants at Kestrel Works (kestrelworks.example). We are a small firm that provides high-end software development and methodology consulting to medium to large enterprise IT organizations.

Our logo uses Futura for the font and we would like to stick with navy blue and canary yellow for the logo colors. Attached are normal and reversed versions of our logos in illustrator format.
Updates

Hi Everyone, Thank yo very much for your amazing design ideas. I have created a poll for this project and our employees will be voting on the design they wish to use. We will be making a decision this Wednesday (October 22nd). Thanks again, Dale Hartwick

Industry/Entity Type

Business

```html
<!DOCTYPE html>
<html lang="en">
<head>
<meta charset="utf-8">
<title>Kestrel Works — Business Card</title>
<link rel="stylesheet" href="https://fonts.googleapis.com/css2?family=Jost:wght@500&family=Open+Sans:wght@400;700&display=swap">
<style>
  :root {
    --navy: #1f4670;
    --canary: #f4e31a;
    --ink: #2e2e2e;
    --paper: #ffffff;
    --backdrop: #e9e7e3;
    --shadow: rgba(40, 30, 20, 0.18);
  }
  * { box-sizing: border-box; margin: 0; padding: 0; }
  html, body { width: 1200px; height: 720px; overflow: hidden; }
  body {
    background: var(--backdrop);
    font-family: "Open Sans", Arial, sans-serif;
    position: relative;
  }
  .card {
    position: absolute;
    top: 205px;
    width: 540px;
    height: 309px;
    background: var(--paper);
    box-shadow: 0 6px 18px var(--shadow);
    overflow: hidden;
  }
  .card--front { left: 40px; }
  .card--back { left: 620px; }

  .wordmark {
    position: absolute;
    display: flex;
    align-items: center;
    color: var(--navy);
    font-family: "Jost", "Futura", sans-serif;
    font-weight: 500;
    text-transform: uppercase;
    white-space: nowrap;
  }
  .wordmark__dot {
    border-radius: 50%;
    background: var(--navy);
    flex: none;
  }
  .card--front .wordmark {
    top: 28px; left: 0; right: 0; justify-content: center;
    font-size: 34px; letter-spacing: 5px; gap: 14px;
  }
  .card--front .wordmark__dot { width: 16px; height: 16px; }

  .contact {
    position: absolute;
    top: 98px;
    left: 0; right: 0;
    display: flex;
    justify-content: center;
    font-size: 12.5px;
    color: var(--ink);
  }
  .contact__col {
    display: flex; flex-direction: column; gap: 9px;
    padding: 0 14px;
  }
  .contact__col--left { align-items: flex-end; border-right: 1px solid #9aa0a6; }
  .contact__col--right { align-items: flex-start; }
  .contact__item { display: flex; align-items: center; gap: 6px; white-space: nowrap; }
  .contact__icon { width: 12px; height: 12px; fill: var(--ink); flex: none; }

  .swoosh { position: absolute; inset: 0; width: 100%; height: 100%; }

  .holder {
    position: absolute;
    left: 60px; top: 256px;
    width: 120px;
    color: var(--paper);
    text-align: center;
  }
  .holder__name { font-weight: 700; font-size: 16px; line-height: 1.2; }
  .holder__title { font-size: 12px; opacity: 0.9; }

  .card--back .wordmark {
    top: 112px; left: 0; right: 0; justify-content: center;
    font-size: 44px; letter-spacing: 7px; gap: 16px;
  }
  .card--back .wordmark__dot { width: 20px; height: 20px; }
  .back-url {
    position: absolute;
    top: 212px; left: 0; right: 0;
    text-align: center;
    font-size: 17px;
    letter-spacing: 2.5px;
    color: var(--ink);
  }
</style>
</head>
<body>

<section class="card card--front" aria-label="Business card front">
  <svg class="swoosh" viewBox="0 0 540 309" aria-hidden="true">
    <path d="M0,232 C180,226 340,178 540,150" fill="none" stroke="var(--canary)" stroke-width="6"/>
    <path d="M0,240 C180,234 340,186 540,158 L540,196 C400,206 280,250 200,309 L0,309 Z" fill="var(--navy)"/>
    <path d="M540,204 C405,214 288,256 212,309" fill="none" stroke="var(--canary)" stroke-width="3.5"/>
  </svg>

  <div class="wordmark">
    <span class="wordmark__dot"></span>
    <span class="wordmark__name">Kestrel Works</span>
  </div>

  <div class="contact">
    <div class="contact__col contact__col--left">
      <span class="contact__item">
        <svg class="contact__icon" viewBox="0 0 24 24" aria-hidden="true"><path d="M6.6 10.8a15.1 15.1 0 0 0 6.6 6.6l2.2-2.2a1 1 0 0 1 1-.25 11.4 11.4 0 0 0 3.6.57 1 1 0 0 1 1 1V20a1 1 0 0 1-1 1A17 17 0 0 1 3 4a1 1 0 0 1 1-1h3.5a1 1 0 0 1 1 1c0 1.25.2 2.46.57 3.6a1 1 0 0 1-.25 1z"/></svg>
        012-555-0147
      </span>
      <span class="contact__item">
        <svg class="contact__icon" viewBox="0 0 24 24" aria-hidden="true"><path d="M12 2a7 7 0 0 0-7 7c0 5.250 7 13 7 13s7-7.75 7-13a7 7 0 0 0-7-7zm0 9.5a2.5 2.5 0 1 1 0-5 2.5 2.5 0 0 1 0 5z"/></svg>
        Harbor City, Millbrook, IL
      </span>
    </div>
    <div class="contact__col contact__col--right">
      <span class="contact__item">
        <svg class="contact__icon" viewBox="0 0 24 24" aria-hidden="true"><path d="M2 5h20v14H2zm2 2v.5l8 5 8-5V7z"/></svg>
        info@kestrelworks.example
      </span>
      <span class="contact__item">
        <svg class="contact__icon" viewBox="0 0 24 24" aria-hidden="true"><path d="M12 2a10 10 0 1 0 0 20 10 10 0 0 0 0-20zm6.9 9h-3a15 15 0 0 0-1.3-5.6A8 8 0 0 1 18.9 11zM12 4.1c.9 1.2 1.8 3.6 1.9 6.9h-3.8c.1-3.3 1-5.7 1.9-6.9zM9.4 5.4A15 15 0 0 0 8.1 11h-3a8 8 0 0 1 4.3-5.6zM5.1 13h3a15 15 0 0 0 1.3 5.6A8 8 0 0 1 5.1 13zm6.9 6.9c-.9-1.2-1.8-3.6-1.9-6.9h3.8c-.1 3.3-1 5.7-1.9 6.9zm2.6-1.3a15 15 0 0 0 1.3-5.6h3a8 8 0 0 1-4.3 5.6z"/></svg>
        www.kestrelworks.example
      </span>
    </div>
  </div>

  <div class="holder">
    <p class="holder__name">Your Name</p>
    <p class="holder__title">Title</p>
  </div>
</section>

<section class="card card--back" aria-label="Business card back">
  <div class="wordmark">
    <span class="wordmark__dot"></span>
    <span class="wordmark__name">Kestrel Works</span>
  </div>
  <p class="back-url">www.kestrelworks.example</p>
</section>

</body>
</html>
```